Hello my name is Colin, I am Starting a business called Lumen Wellness and fitness and am in need of a memorable business card.
It is a personal training studio. I have added the logo that i would like to be on the left center om my business card. i would like room left up the top for a heading sentence such as. "Is your body shocking for all the wrong reasons". there must be room left on the right of the logo below the main heading for 3 sub headings.
then under those 3 headings and logo room for another larger heading eg. "give me a call and learn how to eat chocolate, drink bear and have great sex". in what room is left i would like to be used for my contact details, use I'm Colin Ferrante your fitness expert on the left then on the right Phone, Email and website space in at least 12 Point. Very specific i know :) now onto the back, for the back i would like an eye catching graphic and room for one main headline and 3 bullet points centered just write anything i will choose what to put in them when i pick a winner. Thank you very much for sticking through all of that :) i appreciate you taking the time to read it and hopefully undergo designing me a business card.
I can't wait to see the designs!

Target Market(s)

slightly more towards females although it would probably be best if it was targeted towards both sexes

Industry/Entity Type

Training

Requirements
Nice to have
• I would love to see if anyone could come up with a design that would really make my card stand out and be memorable.
Should not have
• tacky fitness photos of abs and muscles etc.

```html
<!DOCTYPE html>
<html lang="en">
<head>
<meta charset="utf-8">
<title>Lumen Wellness and Fitness – Business Cards</title>
<link rel="stylesheet" href="https://fonts.googleapis.com/css2?family=Jost:wght@400;500;600;700&display=swap">
<style>
  :root {
    --stage: #e8e5e1;
    --paper: #ffffff;
    --navy: #1d4676;
    --navy-deep: #163a66;
    --ink: #222222;
    --ink-soft: #444444;
    --charcoal: #2c2c2c;
    --rule: #9a9a9a;
    --blush-light: #efe2d6;
    --blush-mid: #e3cbbd;
    --faint-on-white: #e6e8ee;
    --faint-on-navy: #3a5f8c;
  }
  * { box-sizing: border-box; margin: 0; padding: 0; }
  html, body { width: 1200px; height: 745px; overflow: hidden; }
  body {
    background: var(--stage);
    font-family: "Jost", sans-serif;
    position: relative;
  }
  .card {
    position: absolute;
    width: 525px;
    height: 299px;
    overflow: hidden;
    box-shadow: 0 2px 6px rgba(0,0,0,.25);
  }

  /* Front */
  .card-front { left: 53px; top: 53px; background: var(--paper); }
  .front-heading {
    position: absolute; left: 30px; top: 40px; width: 250px;
    text-align: center; color: var(--navy);
    font-weight: 600; font-size: 16px; line-height: 1.2;
  }
  .front-brand {
    position: absolute; left: 42px; top: 104px; width: 230px;
    color: var(--navy); font-weight: 500; line-height: 1;
  }
  .front-brand .brand-name { display: block; font-size: 60px; letter-spacing: -1px; }
  .front-brand .brand-sub { display: block; font-size: 15px; margin-top: 2px; padding-left: 60px; }
  .front-divider {
    position: absolute; left: 278px; top: 12px; width: 1px; height: 208px;
    background: var(--rule);
  }
  .front-details { position: absolute; left: 290px; top: 14px; width: 230px; color: var(--ink-soft); }
  .front-details .intro { font-size: 11.5px; line-height: 1.25; }
  .front-details .points { list-style: none; margin-top: 13px; font-size: 11.5px; line-height: 1.55; }
  .front-details .points li::before { content: "• "; }
  .front-details .callout {
    margin-top: 14px; font-weight: 600; font-size: 14px; line-height: 1.2; color: #3a3a3a;
  }
  .front-details .callout span { display: block; }
  .front-details .callout .gap { margin-top: 5px; }
  .name-band {
    position: absolute; left: 0; top: 224px; width: 100%; height: 33px;
    background: var(--charcoal); color: #fff;
    display: flex; align-items: center; justify-content: center; gap: 5px;
  }
  .name-band .person { font-weight: 700; font-size: 18px; }
  .name-band .role { font-size: 15px; }
  .contact-band {
    position: absolute; left: 0; top: 259px; width: 100%; height: 40px;
    background: linear-gradient(90deg, var(--navy-deep), var(--navy));
    color: #fff; font-size: 16px;
    display: flex; align-items: center; justify-content: center; gap: 14px;
  }
  .contact-band .item { display: flex; align-items: center; gap: 4px; }
  .contact-band svg { width: 14px; height: 14px; }

  /* Backs */
  .back-headline { position: absolute; left: 0; width: 100%; text-align: center; font-size: 22px; }
  .back-points { position: absolute; list-style: none; font-size: 24px; line-height: 30px; }
  .back-points li::before { content: "● "; font-size: 19px; vertical-align: 2px; }
  .back-web {
    position: absolute; left: 0; width: 100%; text-align: center;
    font-weight: 500; font-size: 20px; letter-spacing: 3px;
  }
  .back-mark {
    position: absolute; left: 60px; top: 50px; line-height: 1; font-weight: 500;
  }
  .back-mark .brand-name { display: block; font-size: 120px; letter-spacing: -2px; }
  .back-mark .brand-sub { display: block; font-size: 30px; padding-left: 100px; }

  .card-pattern { left: 603px; top: 60px; color: var(--ink); }
  .card-pattern .pattern-fill {
    position: absolute; inset: 0;
    background: radial-gradient(ellipse at 55% 60%, var(--blush-mid), var(--blush-light) 70%);
  }
  .card-pattern .back-headline { top: 84px; }
  .card-pattern .back-points { left: 141px; top: 118px; }
  .card-pattern .back-web { top: 255px; color: var(--ink); }

  .card-white { left: 56px; top: 394px; background: var(--paper); color: var(--ink-soft); }
  .card-white .back-mark { color: var(--faint-on-white); }
  .card-white .back-headline { top: 85px; }
  .card-white .back-points { left: 142px; top: 118px; }
  .card-white .back-web { top: 256px; color: var(--ink-soft); }

  .card-navy { left: 615px; top: 400px; background: linear-gradient(180deg, var(--navy), var(--navy-deep)); color: #fff; }
  .card-navy .back-mark { color: var(--faint-on-navy); }
  .card-navy .back-headline { top: 85px; }
  .card-navy .back-points { left: 141px; top: 118px; }
  .card-navy .back-web { top: 256px; color: #fff; }
</style>
</head>
<body>

<section class="card card-front" aria-label="Business card front">
  <p class="front-heading">Is your body shocking for all the wrong reasons</p>
  <div class="front-brand">
    <span class="brand-name">Lumen</span>
    <span class="brand-sub">Wellness and Fitness</span>
  </div>
  <div class="front-divider"></div>
  <div class="front-details">
    <p class="intro">Lorem ipsum Lorem ipsum<br>Lorem ipsum</p>
    <ul class="points">
      <li>Lorem ipsum diet</li>
      <li>Lorem ipsum diet</li>
      <li>Lorem ipsum diet</li>
    </ul>
    <p class="callout">
      <span>Give me a call and</span>
      <span>Learn how to eat chocolate</span>
      <span>drink bear</span>
      <span class="gap">Have great sex</span>
    </p>
  </div>
  <div class="name-band">
    <span class="person">Colin Ferrante,</span><span class="role">Fitness expert</span>
  </div>
  <div class="contact-band">
    <span class="item">
      <svg viewBox="0 0 16 16"><circle cx="8" cy="8" r="7" fill="none" stroke="#fff" stroke-width="1.3"/><path d="M5.5 4.5l1.5 1.5-1 1c.6 1.3 1.6 2.3 2.9 2.9l1-1 1.6 1.5-1 1.2C7.7 11.6 4.7 8.6 4.3 5.6z" fill="#fff"/></svg>
      0123 456789
    </span>
    <span class="item">
      <svg viewBox="0 0 16 16"><rect x="1.5" y="4" width="13" height="9" fill="none" stroke="#fff" stroke-width="1.4"/><path d="M1.5 4l6.5 5 6.5-5" fill="none" stroke="#fff" stroke-width="1.4"/></svg>
      info@lumenwellness.com
    </span>
    <span class="item">
      <svg viewBox="0 0 16 16"><circle cx="8" cy="8" r="6.5" fill="none" stroke="#fff" stroke-width="1.2"/><ellipse cx="8" cy="8" rx="3" ry="6.5" fill="none" stroke="#fff" stroke-width="1.1"/><path d="M1.5 8h13M2.5 5h11M2.5 11h11" stroke="#fff" stroke-width="1"/></svg>
      www.lumenwellness.com
    </span>
  </div>
</section>

<section class="card card-pattern" aria-label="Business card back, patterned">
  <div class="pattern-fill" role="img" aria-label="Soft blush ornamental paisley and floral swirl pattern filling the card"></div>
  <p class="back-headline">Lorem Ispum Lorem Ispum Lorem Ispum</p>
  <ul class="back-points">
    <li>Lorem Ispum Lorem</li>
    <li>Lorem Ispum Lorem</li>
    <li>Lorem Ispum Lorem</li>
  </ul>
  <p class="back-web">www.lumenfit.com</p>
</section>

<section class="card card-white" aria-label="Business card back, white">
  <div class="back-mark" aria-hidden="true">
    <span class="brand-name">Lumen</span>
    <span class="brand-sub">Wellness and Fitness</span>
  </div>
  <p class="back-headline">Lorem Ispum Lorem Ispum Lorem Ispum</p>
  <ul class="back-points">
    <li>Lorem Ispum Lorem</li>
    <li>Lorem Ispum Lorem</li>
    <li>Lorem Ispum Lorem</li>
  </ul>
  <p class="back-web">www.lumenfit.com</p>
</section>

<section class="card card-navy" aria-label="Business card back, navy">
  <div class="back-mark" aria-hidden="true">
    <span class="brand-name">Lumen</span>
    <span class="brand-sub">Wellness and Fitness</span>
  </div>
  <p class="back-headline">Lorem Ispum Lorem Ispum Lorem Ispum</p>
  <ul class="back-points">
    <li>Lorem Ispum Lorem</li>
    <li>Lorem Ispum Lorem</li>
    <li>Lorem Ispum Lorem</li>
  </ul>
  <p class="back-web">www.lumenfit.com</p>
</section>

</body>
</html>
```